New website for salon services and wedding hair and makeup

I am a professional hairstylist and makeup artist in Charleston, SC. I have my own company where I see clients for cut and color and I also go on site for weddings. I have a current website that I would like to update and change the style. I would like to add a contact form, map, additional pages and be mobile friendly. It is important to me that it have a site map and can show up in searches. I will need to add photos to the site every so often and would like to continue to work with the designer. I have a logo that I am happy with and have attached the file however if you think a new logo would help the look of the site I am open to it. My current website is www.brightcombstudio-example.com, I would like to change the style and layout so it looks up to date. Here are some links to sites that I like the look of but I don't want to limit your creativity. http://willowlanefolio-example.com/ http://www.runwaylensworks-example.com http://miraventhol-example.com/. I have attached a few files for mock up purposes, please let me know if you would like more content. Thank you!

Target Market(s)

Women, Brides

Industry/Entity Type

Hair And Beauty

Number of Pages Required

1 page

Font styles to use
Sans Serif
Script

Requirements
Must have
• Contact form, Mobile friendly, sitemap
Nice to have
• I really like the look for the sites I have included on the project description guide.
Should not have
• Nothing overly girly.

```html
<!DOCTYPE html>
<html lang="en">
<head>
<meta charset="utf-8">
<title>Bright Comb Studio – Hair and Makeup</title>
<link href="https://fonts.googleapis.com/css2?family=Open+Sans:wght@400;600;700&family=Great+Vibes&display=swap" rel="stylesheet">
<style>
:root{
  --teal:#5ad3df;
  --teal-dark:#3fbccb;
  --ink:#2f3a44;
  --grey:#777;
  --line:#dcdcdc;
  --footer:#4b4b4d;
  --footer-text:#cfcfcf;
  --social:#d8454f;
  --white:#fff;
}
*{box-sizing:border-box;margin:0;padding:0}
html,body{width:800px;height:1200px;overflow:hidden}
body{font-family:"Open Sans",Arial,sans-serif;color:var(--ink);background:var(--white);position:relative}

.top-nav{position:absolute;top:0;left:0;width:800px;height:50px;border-bottom:1px solid var(--line);display:flex;justify-content:center}
.top-nav ul{list-style:none;display:flex;border-left:1px solid var(--line)}
.top-nav li{font-size:10px;font-weight:600;letter-spacing:1px;padding:0 20px;line-height:48px;border-right:1px solid var(--line)}

.header{position:absolute;top:50px;left:0;width:800px;height:123px}
.search{position:absolute;left:80px;top:46px;width:108px;height:26px;border:1px solid var(--line);font-size:10px;color:#aaa;display:flex;align-items:center;padding-left:8px;gap:6px}
.brand{position:absolute;left:300px;top:40px;width:200px;text-align:center;font-size:20px;font-weight:600;color:var(--teal-dark);letter-spacing:1px}
.follow{position:absolute;right:30px;top:47px;display:flex;align-items:center;gap:6px;font-size:9px;color:var(--grey);letter-spacing:.5px}
.follow .dot{width:20px;height:20px;border-radius:50%;background:var(--social)}

.hero{position:absolute;top:173px;left:0;width:800px;height:400px;background:radial-gradient(ellipse at 62% 40%,#c98f6b 0%,#8a5a3e 30%,#3f2e25 65%,#1f1a18 100%)}
.hero-label{position:absolute;font-weight:700;color:var(--teal-dark);background:var(--white);letter-spacing:1px;font-size:17px;padding:6px 14px}
.label-a{left:133px;top:179px}
.label-b{left:272px;top:223px;padding-left:36px}
.amp{position:absolute;left:240px;top:152px;width:86px;height:86px;border-radius:50%;background:var(--teal);color:var(--white);font-family:"Great Vibes",cursive;font-size:66px;text-align:center;line-height:92px}
.arrow{position:absolute;top:182px;width:22px;height:36px;background:rgba(0,0,0,.55);display:flex;align-items:center;justify-content:center}
.arrow-left{left:0}.arrow-right{right:0}
.dots{position:absolute;top:350px;left:0;width:800px;display:flex;justify-content:center;gap:8px}
.dots span{width:9px;height:9px;border-radius:50%;background:rgba(255,255,255,.6)}
.dots span.active{background:var(--white)}

.services{position:absolute;top:573px;left:0;width:800px;height:347px}
.services h2{position:absolute;top:24px;width:800px;text-align:center;font-size:16px;font-weight:700;color:var(--teal-dark);letter-spacing:1px}
.services .rule{position:absolute;top:54px;left:385px;width:30px;height:2px;background:var(--teal)}
.service-grid{position:absolute;top:108px;left:40px;width:720px;display:grid;grid-template-columns:repeat(4,1fr);text-align:center}
.service-icon{width:82px;height:82px;border-radius:50%;background:var(--teal);margin:0 auto;display:flex;align-items:center;justify-content:center}
.service h3{margin-top:22px;font-size:13px;font-weight:700;letter-spacing:.5px}
.service p{margin-top:12px;font-size:9.5px;line-height:1.55;color:var(--grey);height:44px}
.read-more{display:inline-block;margin-top:16px;font-size:9.5px;font-weight:700;letter-spacing:1px;color:var(--teal-dark)}

.footer{position:absolute;top:920px;left:0;width:800px;height:280px;background:var(--footer);color:var(--footer-text)}
.footer h4{font-size:10px;font-weight:700;color:var(--white);letter-spacing:1px;margin-bottom:14px}
.f-col{position:absolute;top:36px;font-size:9.5px;line-height:1.7}
.f-about{left:67px;width:220px}
.f-menu{left:345px}
.f-follow{left:440px}
.f-contact{left:573px}
.f-list{list-style:none}
.f-list li{display:flex;align-items:center;gap:8px}
.f-list .ic{width:10px;height:10px;border-radius:50%;background:var(--footer-text)}
.copyright{position:absolute;top:232px;left:67px;width:666px;border-top:1px solid #666;padding-top:12px;font-size:9px}
</style>
</head>
<body>

<nav class="top-nav">
  <ul><li>HOME</li><li>ABOUT</li><li>SERVICES</li><li>GALLERY</li><li>CONTACT</li></ul>
</nav>

<header class="header">
  <div class="search">
    <svg width="10" height="10" viewBox="0 0 10 10"><circle cx="4" cy="4" r="3" fill="none" stroke="#aaa" stroke-width="1.3"/><line x1="6.3" y1="6.3" x2="9" y2="9" stroke="#aaa" stroke-width="1.3"/></svg>
    Search
  </div>
  <div class="brand">Bright Comb Studio</div>
  <div class="follow">FOLLOW US ON <span class="dot"></span><span class="dot"></span><span class="dot"></span></div>
</header>

<section class="hero" role="img" aria-label="Photo of a woman with styled hair and makeup">
  <div class="hero-label label-a">WEDDING HAIR</div>
  <div class="hero-label label-b">MAKEUP</div>
  <div class="amp">&amp;</div>
  <div class="arrow arrow-left"><svg width="8" height="12" viewBox="0 0 8 12"><path d="M6 1 1 6l5 5" fill="none" stroke="#fff" stroke-width="2"/></svg></div>
  <div class="arrow arrow-right"><svg width="8" height="12" viewBox="0 0 8 12"><path d="M2 1l5 5-5 5" fill="none" stroke="#fff" stroke-width="2"/></svg></div>
  <div class="dots"><span class="active"></span><span></span><span></span><span></span></div>
</section>

<section class="services">
  <h2>OUR SERVICES</h2>
  <div class="rule"></div>
  <div class="service-grid">
    <div class="service">
      <div class="service-icon"><svg width="36" height="40" viewBox="0 0 36 40"><path d="M13 2v8l-4 8 2 2-7 18h28l-7-18 2-2-4-8V2" fill="none" stroke="#2f3a44" stroke-width="2" stroke-linejoin="round"/></svg></div>
      <h3>BRIDAL</h3>
      <p>Thank you for your interest in our<br>on-location bridal services.</p>
      <span class="read-more">READ MORE ›</span>
    </div>
    <div class="service">
      <div class="service-icon"><svg width="38" height="38" viewBox="0 0 38 38"><circle cx="9" cy="29" r="5" fill="none" stroke="#2f3a44" stroke-width="2.5"/><circle cx="29" cy="29" r="5" fill="none" stroke="#2f3a44" stroke-width="2.5"/><path d="M12 25 30 4M26 25 8 4" stroke="#2f3a44" stroke-width="2.5"/></svg></div>
      <h3>HAIR CUT</h3>
      <p>Women $50<br>Men $30</p>
      <span class="read-more">READ MORE ›</span>
    </div>
    <div class="service">
      <div class="service-icon"><svg width="38" height="38" viewBox="0 0 38 38"><path d="M6 34 18 22" stroke="#2f3a44" stroke-width="4" stroke-linecap="round"/><path d="M18 22 32 8M20 24l14-14M21 17l3 3M24 14l3 3M27 11l3 3" stroke="#2f3a44" stroke-width="2"/></svg></div>
      <h3>COLOUR</h3>
      <p>Partial Highlights $100+<br>Full Highlights $140+</p>
      <span class="read-more">READ MORE ›</span>
    </div>
    <div class="service">
      <div class="service-icon"><svg width="40" height="38" viewBox="0 0 40 38"><path d="M4 8h22a8 8 0 0 1 0 16H20l-3 12h-6l2-12H4z" fill="#2f3a44"/><path d="M32 12h6M32 20h6" stroke="#2f3a44" stroke-width="2"/></svg></div>
      <h3>STYLING AND<br>TREATMENTS</h3>
      <p>Blow out/Hair Styling $50<br>Event Updos $85</p>
      <span class="read-more">READ MORE ›</span>
    </div>
  </div>
</section>

<footer class="footer">
  <div class="f-col f-about">
    <h4>ABOUT US</h4>
    <p>Bright Comb Studio specializes in providing gorgeous, long lasting hair and makeup. With over nine years of experience and training, we know how to make your day the very best. We take pride in client satisfaction and helping you achieve the look of your dreams while making the experience memorable and enjoyable.</p>
  </div>
  <div class="f-col f-menu">
    <h4>MENU</h4>
    <ul class="f-list"><li>Home</li><li>About</li><li>Services</li><li>Gallery</li><li>Contact</li></ul>
  </div>
  <div class="f-col f-follow">
    <h4>FOLLOW US ON</h4>
    <ul class="f-list" style="line-height:2.4"><li><span class="ic"></span>Facenote</li><li><span class="ic"></span>Chirper</li><li><span class="ic"></span>Snapgram</li></ul>
  </div>
  <div class="f-col f-contact">
    <h4>CONTACT US</h4>
    <ul class="f-list" style="line-height:2.4">
      <li><svg width="10" height="10" viewBox="0 0 10 10"><path d="M2 1l2 2-1 1.5a6 6 0 0 0 2.5 2.5L7 6l2 2-1.5 1.5C4 9 1 6 .5 2.5z" fill="#cfcfcf"/></svg>843-555-0142</li>
      <li><svg width="10" height="8" viewBox="0 0 10 8"><rect x=".5" y=".5" width="9" height="7" fill="none" stroke="#cfcfcf"/><path d="M.5.5 5 4.5 9.5.5" fill="none" stroke="#cfcfcf"/></svg>hello@brightcombstudio-example.com</li>
    </ul>
  </div>
  <div class="copyright">Copyright © 2015 All Rights Reserved</div>
</footer>

</body>
</html>
```